Swing Dance Themed Cleaning Company Website

We need a website designed for a cleaning company based in Portland, Oregon called Foxtrot Lane. We clean homes and commercial buildings, inside and out.

needs to be vintage and like the velvet tambour. Speakeasy 1920s feel.
needs to be classy.

Check out foxtrotlane.com We are not happy with the site currently.

please look at house scout site for more content https://www.housescoutpro.com/rated.FoxtrotLaneCleaning.48217705.html

Check out my videos on my ClipHaven channel Foxtrot Lane

Target Market(s)

middle class and home owner

Industry/Entity Type

Cleaning Service

Number of Pages Required

3 page

Font styles to use
Other font styles liked:
• jazzrag

Colors

Designer to choose colors to be used in the design.

Requirements
Must have
• must be good on pc and mobile

```html
<!DOCTYPE html>
<html lang="en">
<head>
<meta charset="utf-8">
<title>Foxtrot Lane – Keep Cleaning Classy Portland</title>
<link href="https://fonts.googleapis.com/css2?family=Poiret+One&family=Poppins:wght@400;500;600;700;800&family=Open+Sans:wght@400;600&display=swap" rel="stylesheet">
<style>
:root{
  --orange:#ee6a1c;
  --orange-dark:#d9571a;
  --ink:#1c1c1c;
  --text:#3a3a3a;
  --wood-a:#f1ddb6;
  --wood-b:#e6cc9c;
  --white:#ffffff;
  --shadow:#c9ab7a;
}
*{margin:0;padding:0;box-sizing:border-box}
html,body{width:1200px;height:3429px;overflow:hidden}
body{
  position:relative;
  font-family:"Poppins",sans-serif;color:var(--text);
  background:linear-gradient(100deg,var(--wood-a) 0%,var(--wood-b) 30%,var(--wood-a) 55%,var(--wood-b) 80%,var(--wood-a) 100%);
}
.abs{position:absolute}
.deco{font-family:"Poiret One",sans-serif;font-weight:400;color:var(--orange);text-transform:uppercase;letter-spacing:1px}
.btn{position:absolute;display:flex;align-items:center;justify-content:center;border-radius:22px;background:var(--orange);color:var(--white);font-size:15px;font-weight:500}

/* header */
.search{left:137px;top:39px;width:133px;height:32px;border:2px solid var(--orange);display:flex;align-items:center;gap:8px;padding-left:10px;font-size:13px;color:var(--ink)}
.brand{left:420px;top:24px;width:360px;text-align:center}
.brand-name{font-family:"Poppins",sans-serif;font-weight:800;font-size:42px;line-height:1;color:var(--ink);text-transform:uppercase}
.brand-tag{font-size:13px;font-weight:600;color:var(--ink);margin-top:18px;letter-spacing:.5px}
.call{left:858px;top:38px;display:flex;gap:12px;align-items:center}
.call small{display:block;font-size:14px;color:var(--ink)}
.call strong{display:block;font-size:17px;color:var(--orange);font-weight:700}
.rule{left:137px;width:926px;height:1px;background:#b9a07a}
.nav{top:152px;left:0;width:1200px;height:28px}
.nav a{position:absolute;font-size:16px;font-weight:500;color:var(--ink);text-decoration:none}
.nav a.active{color:var(--orange)}

/* hero */
.hero{left:0;top:210px;width:1200px;height:579px;background:linear-gradient(180deg,#8d8d8b,#6f6c66 55%,#7a7055)}
.hero-title{left:0;top:430px;width:1200px;text-align:center;color:var(--white);font-family:"Poiret One",sans-serif;font-size:46px;line-height:62px;text-transform:uppercase;text-shadow:0 2px 4px rgba(0,0,0,.4)}

/* about */
.about-h{left:107px;top:862px;font-size:46px}
.about-lead{left:107px;top:926px;font-size:15px;color:var(--ink)}
.about-sub{left:107px;top:962px;font-size:26px}
.about-p{left:107px;top:1008px;width:500px;font-size:15px;line-height:25px;color:var(--ink)}
.about-img{left:617px;top:860px;width:476px;height:310px;background:linear-gradient(135deg,#d9d9d6,#9fa59a 60%,#c8c2a4);box-shadow:6px 8px 14px rgba(0,0,0,.35)}

/* services */
.sec-h{left:0;width:1200px;text-align:center;font-size:46px}
.sec-line{left:555px;width:90px;height:5px;border-top:1px solid #a88d66;border-bottom:1px solid #a88d66}
.svc-img{top:1390px;width:318px;height:215px}
.svc-box{top:1530px;width:259px;height:226px;clip-path:polygon(0 22%,100% 0,100% 100%,0 100%);padding:76px 14px 0 14px;border-bottom:3px solid var(--orange)}
.svc-box h3{font-size:15px;font-weight:500;margin-bottom:14px}
.svc-box p{font-size:12px;line-height:26px}
.svc-box.light{background:var(--white)}
.svc-box.light h3{color:var(--orange)}
.svc-box.light p{color:var(--text)}
.svc-box.accent{background:var(--orange);border-bottom-color:var(--orange-dark)}
.svc-box.accent h3,.svc-box.accent p{color:var(--white)}

/* pricing */
.price-shadow{left:114px;top:1905px;width:951px;height:312px;background:var(--shadow);clip-path:polygon(0 0,100% 4%,100% 100%,3% 100%)}
.price-card{left:133px;top:1884px;width:900px;height:300px;background:var(--orange);clip-path:polygon(0 0,100% 6%,98% 100%,2% 96%)}
.price-h{left:181px;top:1900px;font-size:46px;color:var(--white)}
.price-text{left:181px;top:1966px;width:560px;font-size:17px;font-weight:600;line-height:28px;color:var(--white)}
.price-btn{left:183px;top:2110px;width:139px;height:43px;background:var(--white);color:var(--orange)}
.price-art{left:735px;top:1898px;width:270px;height:262px;background:radial-gradient(circle,#f7a25e,var(--orange) 70%)}

/* blog */
.blog-img{top:2437px;width:265px;height:183px}
.blog-t{top:2640px;width:265px;font-size:15px;font-weight:700;line-height:25px;color:var(--orange)}
.blog-p{top:2706px;width:265px;font-size:12px;line-height:25px;color:var(--ink)}
.blog-btn{top:2793px;width:142px;height:44px}

/* footer */
.footer{left:0;top:2944px;width:1200px;height:485px;background:linear-gradient(100deg,#f3e3c2,#ead5aa 50%,#f3e3c2)}
.f-brand{left:130px;top:3048px;font-family:"Poppins",sans-serif;font-weight:800;font-size:46px;line-height:1;color:var(--ink);text-transform:uppercase}
.f-tag{left:120px;top:3146px;font-size:17px;font-weight:600;color:var(--ink)}
.social{left:127px;top:3192px;display:flex;gap:8px}
.social span{width:18px;height:18px;border-radius:50%;background:#2f5fa8;display:block}
.f-col h4{font-size:16px;font-weight:600;color:var(--ink);margin-bottom:14px}
.f-col li{list-style:none;font-size:14px;line-height:26px;color:var(--ink);display:flex;align-items:center;gap:6px}
.news-h{left:185px;top:3278px;font-size:22px;font-weight:700;color:var(--ink)}
.news-s{left:185px;top:3312px;font-size:12px;color:var(--ink)}
.news-in{left:523px;top:3285px;width:282px;height:38px;background:#f7ecd3;border:1px solid #d9c49c;font-size:11px;color:var(--ink);padding:12px}
.news-btn{left:805px;top:3285px;width:121px;height:38px;background:var(--orange-dark);color:var(--white);font-size:14px;font-weight:600;display:flex;align-items:center;justify-content:center}
.copy{left:0;top:3372px;width:1200px;text-align:center;font-family:"Open Sans",sans-serif;font-size:16px;color:var(--ink)}
</style>
</head>
<body>

<header>
  <div class="abs search">
    <svg width="14" height="14" viewBox="0 0 14 14"><circle cx="6" cy="6" r="4.5" fill="none" stroke="#1c1c1c" stroke-width="1.6"/><line x1="9.3" y1="9.3" x2="13" y2="13" stroke="#1c1c1c" stroke-width="1.6"/></svg>
    Search
  </div>
  <div class="abs brand">
    <div class="brand-name">Foxtrot Lane</div>
    <div class="brand-tag">KEEP CLEANING CLASSY PORTLAND</div>
  </div>
  <div class="abs call">
    <svg width="30" height="30" viewBox="0 0 24 24"><path d="M6.6 10.8c1.4 2.8 3.8 5.1 6.6 6.6l2.2-2.2c.3-.3.7-.4 1-.2 1.1.4 2.3.6 3.6.6.6 0 1 .4 1 1V20c0 .6-.4 1-1 1C10.6 21 3 13.4 3 4c0-.6.4-1 1-1h3.5c.6 0 1 .4 1 1 0 1.3.2 2.5.6 3.6.1.3 0 .7-.2 1z" fill="#1c1c1c"/></svg>
    <div><small>Call us</small><strong>503-555-0148</strong></div>
  </div>
  <div class="abs rule" style="top:110px"></div>
  <nav class="abs nav">
    <a class="active" style="left:306px">Home</a>
    <a style="left:414px">About us</a>
    <a style="left:546px">Our Services</a>
    <a style="left:708px">Blog</a>
    <a style="left:803px">Contact us</a>
  </nav>
</header>

<section>
  <div class="abs hero" role="img" aria-label="Photo of a cleaning crew in aprons tidying a bright living room"></div>
  <h1 class="abs hero-title">Residential Cleaning Services<br>Success in Every Projects</h1>
</section>

<section>
  <h2 class="abs deco about-h">About Us</h2>
  <p class="abs about-lead">Making the greater Portland area clean, one building at a time</p>
  <h3 class="abs deco about-sub">Good People, Great Service</h3>
  <p class="abs about-p">Foxtrot Lane is a family owned professional cleaning business. We provide our years of cleaning experience to homes and businesses in and around Portland, Oregon.</p>
  <div class="btn" style="left:107px;top:1109px;width:142px;height:44px">Read More</div>
  <div class="btn" style="left:265px;top:1109px;width:158px;height:44px">Leave a Review</div>
  <div class="abs about-img" role="img" aria-label="Photo of a cleaner in yellow gloves wiping a table"></div>
</section>

<section>
  <h2 class="abs deco sec-h" style="top:1280px">Our Services</h2>
  <div class="abs sec-line" style="top:1342px"></div>

  <div class="abs svc-img" style="left:107px;background:linear-gradient(160deg,#d8dde0,#6f7d86)" role="img" aria-label="Photo of a maid holding cleaning supplies in a kitchen"></div>
  <div class="abs svc-box light" style="left:139px"><h3>Cleaning &amp; Maid Services</h3><p>Sed ut perspiciatis unde omnis iste natus error sit voluptatem accusanti-um doloremque laudantium</p></div>

  <div class="abs svc-img" style="left:441px;background:linear-gradient(160deg,#c9d3d6,#5e6a6e)" role="img" aria-label="Photo of a worker cleaning carpet in an office"></div>
  <div class="abs svc-box accent" style="left:473px"><h3>Carpet Cleaning</h3><p>Sed ut perspiciatis unde omnis iste natus error sit voluptatem accusanti-um doloremque laudantium</p></div>

  <div class="abs svc-img" style="left:775px;background:linear-gradient(160deg,#e0e2e0,#7c807c)" role="img" aria-label="Photo of a cleaner washing a window"></div>
  <div class="abs svc-box light" style="left:807px"><h3>Window Washing</h3><p>Sed ut perspiciatis unde omnis iste natus error sit voluptatem accusanti-um doloremque laudantium</p></div>
</section>

<section>
  <div class="abs price-shadow"></div>
  <div class="abs price-card"></div>
  <h2 class="abs deco price-h">Pricing:</h2>
  <p class="abs price-text">$80 per 1,000 square feet for usual housekeeping services,<br>call for an&nbsp; estimate for other services<br><span style="display:block;height:6px"></span>To Schedule an Appointment or get an estimate Call<br><span style="display:block;height:6px"></span>503 - 555 - 0148 Or email hello@foxtrotlane.com</p>
  <div class="btn price-btn">Read More</div>
  <div class="abs price-art" role="img" aria-label="Line illustration of a dancing gentleman sweeping with a broom"></div>
</section>

<section>
  <h2 class="abs deco sec-h" style="top:2300px">From Our Blog</h2>
  <div class="abs sec-line" style="top:2364px"></div>

  <div class="abs blog-img" style="left:137px;background:linear-gradient(160deg,#e9e6e2,#9a8f86)" role="img" aria-label="Photo of a smiling cleaner wiping a table"></div>
  <h3 class="abs blog-t" style="left:137px">Lorem Ipsum is simply dummy text of the printing</h3>
  <p class="abs blog-p" style="left:137px">Lorem Ipsum is simply dummy text of the printing and typesetting industry, when an unknown printer took a galley</p>
  <div class="btn blog-btn" style="left:198px">Read More</div>

  <div class="abs blog-img" style="left:466px;background:linear-gradient(160deg,#f0efec,#8b9a7c)" role="img" aria-label="Photo of a cleaner dusting near plants"></div>
  <h3 class="abs blog-t" style="left:466px">Lorem Ipsum is simply dummy text of the printing</h3>
  <p class="abs blog-p" style="left:466px">Lorem Ipsum is simply dummy text of the printing and typesetting industry, when an unknown printer took a galley</p>
  <div class="btn blog-btn" style="left:527px">Read More</div>

  <div class="abs blog-img" style="left:795px;background:linear-gradient(160deg,#eceae6,#a48a72)" role="img" aria-label="Photo of a bucket of cleaning supplies and a mop on a floor"></div>
  <h3 class="abs blog-t" style="left:795px">Lorem Ipsum is simply dummy text of the printing</h3>
  <p class="abs blog-p" style="left:795px">Lorem Ipsum is simply dummy text of the printing and typesetting industry, when an unknown printer took a galley</p>
  <div class="btn blog-btn" style="left:857px">Read More</div>
</section>

<footer>
  <div class="abs footer"></div>
  <div class="abs f-brand">Foxtrot<br>Lane</div>
  <div class="abs f-tag">KEEP CLEANING CLASSY PORTLAND</div>
  <div class="abs social"><span></span><span></span><span></span><span></span></div>

  <div class="abs f-col" style="left:503px;top:3040px">
    <h4>Contact us</h4>
    <ul>
      <li><svg width="12" height="12" viewBox="0 0 12 12"><path d="M11 1 1 5.5l4.5 1 1 4.5z" fill="#1c1c1c"/></svg>418 SE Alder St #207,</li>
      <li>Portland, OR 97214</li>
      <li><svg width="12" height="12" viewBox="0 0 24 24"><path d="M6.6 10.8c1.4 2.8 3.8 5.1 6.6 6.6l2.2-2.2c.3-.3.7-.4 1-.2 1.1.4 2.3.6 3.6.6.6 0 1 .4 1 1V20c0 .6-.4 1-1 1C10.6 21 3 13.4 3 4c0-.6.4-1 1-1h3.5c.6 0 1 .4 1 1 0 1.3.2 2.5.6 3.6.1.3 0 .7-.2 1z" fill="#1c1c1c"/></svg>503-555-0148</li>
      <li><svg width="13" height="10" viewBox="0 0 13 10"><rect width="13" height="10" fill="#1c1c1c"/><path d="M0 0l6.5 5L13 0" fill="none" stroke="#f1ddb6" stroke-width="1.2"/></svg>hello@foxtrotlane.com</li>
    </ul>
  </div>
  <div class="abs f-col" style="left:766px;top:3040px">
    <h4>Quick links</h4>
    <ul><li>Home</li><li>About us</li><li>Our services</li><li>Blog</li><li>Contact us</li></ul>
  </div>
  <div class="abs f-col" style="left:942px;top:3040px">
    <h4>Other links</h4>
    <ul><li>Company</li><li>Privacy Policy</li><li>Terms &amp; Conditions</li><li>Our Clients</li></ul>
  </div>

  <div class="abs rule" style="top:3255px"></div>
  <h3 class="abs news-h">NEWSLETTER SUBSCRIBE</h3>
  <p class="abs news-s">Get the scoop on new arrivals and problems</p>
  <div class="abs news-in">Email id</div>
  <div class="abs news-btn">Subscribe</div>
  <div class="abs rule" style="top:3349px"></div>
  <p class="abs copy">Copyright © 2018. All rights reserved</p>
</footer>

</body>
</html>
```